Start-up braucht modernes/hochwertiges Getränkeetikett
Zielgruppe
Wir sind ein modernes, nachhaltiges Start-up, welches eine neue Getränkekategorie auf den Markt bringt. Ein sogenanntes Elektrolyt-Getränk mit dem Namen FLUXO4. Es ist abgefüllt in eine 500 ml Flasche und enthält Magnesium, Kalzium, Kalium, und Natrium. Diese Stoffe (Elektrolyte) dienen der körperlichen Hydrierung. Zu Dehydrierung kann es durch Hitze, Alkohol, Sport oder Krankheit kommen. Krankheit liegt bei uns allerdings nicht im Fokus. In unserer Zielgruppe befinden sich hauptsächlich Personen im Alter von 18 - 29 Jahren.
Die Geschmacksrichtung ist Zitrone-Limette.
Aufgabenstellung
Das Etikett soll:
- MODERN, SCHLICHT und HOCHWERTIG sein, so dass es im Supermarkt hervorsticht
- erkenntlich machen, dass die Stoffe Magnesium, Natrium, Kalzium und Kalium enthalten sind
- sich farblich deutlich von der Farbe des Inhalts (weiß) abheben. (Vorzugsweise mit einem hellen Blau, türkis)
- für unsere junge Zielgruppe ansprechend sein
- ebenfalls auf die Geschmacksrichtung (Zitrone-Limette) hinweisen, und zwar so, dass wenn man eine weitere Geschmacksrichtung auf den Markt bringen möchte, diese leicht angepasst werden kann.
- nicht nach einem Energydrink oder einem typischen Sportgetränk aussehen
- unter dem Namen den Slogan 'Elektrolyt-Getränk' stehen haben
-Das Etikett ist nicht dursichtig sondern besteht aus Papier
Der Name sowie das Logo können selbstverständlich farblich verändert werden. Bei dem Logo können auch größere Änderungen vollzogen werden.
Bitte beachten Sie die unten zu stehenden Regler um sich einen guten Überblick über unsere Vorstellungen zu verschaffen. Die Platzierung des EAN-Code ist für ihr Design irrelevat .
Bei Unklarheiten gerne nachfragen!

```html
<!DOCTYPE html>
<html lang="de">
<head>
<meta charset="utf-8">
<title>FLUXO4 Elektrolyt-Getränk – Etiketten</title>
<link rel="stylesheet" href="https://fonts.googleapis.com/css2?family=Montserrat:ital,wght@0,500;0,600;0,800;1,500&family=Oswald:wght@600&display=swap">
<style>
  :root {
    --backdrop: #e4e6e8;
    --paper: #fdfcf1;
    --teal: #2f6f83;
    --mg: #2a9ad8;
    --ca: #f29a1c;
    --k: #9c2a8e;
    --na: #1f9f8e;
  }
  * { box-sizing: border-box; margin: 0; padding: 0; }
  html, body { width: 1200px; height: 1193px; overflow: hidden; }
  body {
    background: var(--backdrop);
    font-family: "Montserrat", sans-serif;
    position: relative;
  }
  .label {
    position: absolute;
    top: 270px;
    width: 380px;
    height: 640px;
    background: var(--paper);
    box-shadow: 0 6px 24px rgba(0,0,0,.12);
    overflow: hidden;
  }
  .label--citrus { left: 160px; }
  .label--berry { left: 660px; }
  .label__brush { position: absolute; left: 0; top: 200px; width: 380px; height: 320px; }
  .label__frame { position: absolute; left: 26px; top: 250px; width: 330px; height: 240px; }
  .brand {
    position: absolute;
    left: 44px; top: 486px;
    transform: rotate(-90deg);
    transform-origin: left top;
    font-weight: 800;
    font-size: 78px;
    line-height: 1;
    letter-spacing: 1px;
    color: var(--teal);
    white-space: nowrap;
  }
  .slogan {
    position: absolute;
    left: 124px; top: 484px;
    transform: rotate(-90deg);
    transform-origin: left top;
    font-family: "Oswald", sans-serif;
    font-weight: 600;
    font-size: 15px;
    line-height: 1.2;
    letter-spacing: 1px;
    color: var(--teal);
    white-space: nowrap;
  }
  .mineral {
    position: absolute;
    width: 48px; height: 48px;
    border-radius: 50%;
    display: flex; align-items: center; justify-content: center;
    color: #fff;
    font-weight: 800;
    font-size: 19px;
  }
  .mineral--mg { left: 228px; top: 382px; background: var(--mg); }
  .mineral--ca { left: 290px; top: 372px; background: var(--ca); }
  .mineral--k  { left: 200px; top: 432px; background: var(--k); }
  .mineral--na { left: 262px; top: 428px; background: var(--na); }
  .fruit {
    position: absolute;
    left: 186px; top: 500px;
    width: 180px; height: 76px;
    border-radius: 38px;
  }
  .label--citrus .fruit { background: linear-gradient(90deg, #7dbf2e 0%, #a6d63f 45%, #f6cb2a 70%, #f3b81a 100%); }
  .label--berry .fruit { background: linear-gradient(90deg, #d8324e 0%, #c42745 45%, #3f5277 70%, #2e3e5e 100%); }
  .flavour {
    position: absolute;
    top: 594px;
    font-style: italic;
    font-weight: 500;
    font-size: 14px;
    line-height: 1.2;
    color: var(--teal);
    white-space: nowrap;
  }
  .volume {
    position: absolute;
    top: 590px;
    right: 28px;
    font-weight: 600;
    font-size: 15px;
    line-height: 1.2;
    color: var(--teal);
    white-space: nowrap;
  }
  .label--citrus .flavour { left: 150px; }
  .label--berry .flavour { left: 96px; }
</style>
</head>
<body>

<section class="label label--citrus">
  <svg class="label__brush" viewBox="0 0 380 320" role="img" aria-label="Wasseroberfläche mit Luftblasen in hellem Türkis, als Pinselstrich">
    <defs>
      <linearGradient id="water-a" x1="0" y1="0" x2="0" y2="1">
        <stop offset="0" stop-color="#e3f4f7"/>
        <stop offset=".45" stop-color="#a9d8e4"/>
        <stop offset="1" stop-color="#d6eef3"/>
      </linearGradient>
    </defs>
    <path fill="url(#water-a)" d="M0 120 L60 95 L150 80 L250 40 L290 30 L300 60 L380 70 L380 270 L300 275 L220 300 L150 310 L100 290 L40 300 L0 295 Z"/>
  </svg>
  <svg class="label__frame" viewBox="0 0 330 240" aria-hidden="true">
    <path d="M60 2 H2 V238 H150" fill="none" stroke="var(--teal)" stroke-width="4"/>
    <path d="M250 2 H328 V200" fill="none" stroke="var(--teal)" stroke-width="4"/>
  </svg>
  <div class="brand">FLUXO4</div>
  <div class="slogan">ELEKTROLYT-GETRÄNK</div>
  <span class="mineral mineral--mg">Mg</span>
  <span class="mineral mineral--ca">Ca</span>
  <span class="mineral mineral--k">K</span>
  <span class="mineral mineral--na">Na</span>
  <div class="fruit" role="img" aria-label="Halbierte Limette und Zitronenspalte"></div>
  <p class="flavour">Zitrone-Limette</p>
  <p class="volume">500 ml</p>
</section>

<section class="label label--berry">
  <svg class="label__brush" viewBox="0 0 380 320" role="img" aria-label="Wasseroberfläche mit Luftblasen in hellem Türkis, als Pinselstrich">
    <defs>
      <linearGradient id="water-b" x1="0" y1="0" x2="0" y2="1">
        <stop offset="0" stop-color="#e3f4f7"/>
        <stop offset=".45" stop-color="#a9d8e4"/>
        <stop offset="1" stop-color="#d6eef3"/>
      </linearGradient>
    </defs>
    <path fill="url(#water-b)" d="M0 120 L60 95 L150 80 L250 40 L290 30 L300 60 L380 70 L380 270 L300 275 L220 300 L150 310 L100 290 L40 300 L0 295 Z"/>
  </svg>
  <svg class="label__frame" viewBox="0 0 330 240" aria-hidden="true">
    <path d="M60 2 H2 V238 H150" fill="none" stroke="var(--teal)" stroke-width="4"/>
    <path d="M250 2 H328 V200" fill="none" stroke="var(--teal)" stroke-width="4"/>
  </svg>
  <div class="brand">FLUXO4</div>
  <div class="slogan">ELEKTROLYT-GETRÄNK</div>
  <span class="mineral mineral--mg">Mg</span>
  <span class="mineral mineral--ca">Ca</span>
  <span class="mineral mineral--k">K</span>
  <span class="mineral mineral--na">Na</span>
  <div class="fruit" role="img" aria-label="Himbeeren und Heidelbeeren mit Minzblatt"></div>
  <p class="flavour">Himbeere-Heidelbeere</p>
  <p class="volume">500 ml</p>
</section>

</body>
</html>
```